BrindleStaffing Business Card Design

We are a staffing company finding positions for dedicated nurses and physicians.

Target Market(s)

Business Professionals

Industry/Entity Type

Staffing

Contact Information for Business Card

Gordon Pratley
Chairman
417 39th Avenue South
SAINT PETERSBURG FL 33712
813-555-4172 Mobile
813-555-8036 Fax
gpratley@brindlestaffing.com
www.brindlestaffing.com

Font styles to use
Sans Serif

Colors
fbee3e
f04a50
f37122

Requirements
Must have
• Logo Attached, see colors below. We'd like to see Yellow, Orange and Red.

```html
<!DOCTYPE html>
<html lang="en">
<head>
<meta charset="utf-8">
<title>BrindleStaffing Business Card</title>
<link rel="stylesheet" href="https://fonts.googleapis.com/css2?family=Open+Sans:wght@400;600;700;800&display=swap">
<style>
  :root {
    --stage: #202020;
    --card: #1b1b1b;
    --card-edge: #2a2a2a;
    --yellow: #fbee3e;
    --orange: #f37122;
    --red: #f04a50;
    --white: #ffffff;
  }
  html, body {
    margin: 0;
    padding: 0;
    width: 1200px;
    height: 960px;
    overflow: hidden;
    background: var(--stage);
  }
  .canvas {
    position: relative;
    width: 1200px;
    height: 960px;
    font-family: "Open Sans", Arial, sans-serif;
  }
  .card {
    position: absolute;
    left: 250px;
    width: 700px;
    height: 400px;
    display: block;
  }
  .card--back { top: 60px; }
  .card--front { top: 500px; }
  .card-face { fill: var(--card); stroke: var(--card-edge); stroke-width: 1; }
  .wordmark { font-weight: 800; fill: var(--orange); letter-spacing: -1px; }
  .web-line { font-weight: 600; font-size: 17px; fill: var(--white); letter-spacing: 3px; }
  .web-line .web-name { fill: var(--yellow); }
  .band-orange { fill: var(--orange); }
  .tri-yellow { fill: var(--yellow); }
  .tri-red { fill: var(--red); }
  .contact { font-size: 15px; fill: var(--white); }
  .icon { fill: none; stroke: var(--white); stroke-width: 1.4; }
  .person-name { font-size: 22px; font-weight: 700; fill: var(--white); }
  .person-title, .person-address { font-size: 17px; fill: var(--white); }
</style>
</head>
<body>
<main class="canvas">

  <svg class="card card--back" viewBox="0 0 700 400" aria-label="Card back">
    <rect class="card-face" x="0.5" y="0.5" width="699" height="399"/>
    <text class="wordmark" x="350" y="200" font-size="64" text-anchor="middle">BrindleStaffing</text>
    <text class="web-line" x="350" y="248" text-anchor="middle">www.<tspan class="web-name">brindlestaffing</tspan>.com</text>
  </svg>

  <svg class="card card--front" viewBox="0 0 700 400" aria-label="Card front">
    <rect class="card-face" x="0.5" y="0.5" width="699" height="399"/>
    <text class="wordmark" x="36" y="92" font-size="52">BrindleStaffing</text>

    <polygon class="band-orange" points="0,130 455,130 420,205 300,205 272,250 0,250"/>
    <polygon class="tri-yellow" points="210,290 355,290 392,392"/>
    <polygon class="tri-red" points="390,185 700,250 700,400 462,400"/>

    <g class="contact-list">
      <circle class="icon" cx="40" cy="158" r="6"/>
      <text class="contact" x="56" y="163">813-555-4172 Mobile</text>
      <rect class="icon" x="34" y="177" width="12" height="9"/>
      <line class="icon" x1="37" y1="181" x2="43" y2="181"/>
      <text class="contact" x="56" y="186">813-555-8036 Fax</text>
      <rect class="icon" x="34" y="200" width="12" height="9"/>
      <polyline class="icon" points="34,200 40,205 46,200"/>
      <text class="contact" x="56" y="209">gpratley@brindlestaffing.com</text>
      <circle class="icon" cx="40" cy="227" r="6"/>
      <line class="icon" x1="34" y1="227" x2="46" y2="227"/>
      <text class="contact" x="56" y="232">www.brindlestaffing.com</text>
    </g>

    <g class="person">
      <text class="person-name" x="672" y="300" text-anchor="end">Gordon Pratley</text>
      <text class="person-title" x="672" y="324" text-anchor="end">Chairman</text>
      <text class="person-address" x="672" y="356" text-anchor="end">417 39th Avenue South</text>
      <text class="person-address" x="672" y="380" text-anchor="end">Saint petersburg fl 33712</text>
    </g>
  </svg>

</main>
</body>
</html>
```